Current state of Man's Soul Christian view

I would like an improvement of my design or a reimagining of my design to help people visualize what happens to the soul after we die. The second picture "screenshot 2023" is not my design but gives another idea.

For further information, there are 4 "time" frames that could be sectioned off. Eden is one time. Then adam rebellion and pre messiah earth (with hades/ Sheol). The third time frame is Elian death, resurrection with the current state of earth. The 4th time frame is the "heavenly realm" which is across all 3 times and is unchanged.

For color ideas, please see my website www.lanternfieldnotes.org which has my color theme. But the death of Elian I would like in some type of red as well as the death of believers.

My goal is something simple, engaging, and easy to understand. If you have any questions please lmk.
Thank you for considering my project.

```html
<!DOCTYPE html>
<html lang="en">
<head>
<meta charset="utf-8">
<title>Current State of Man's Soul</title>
<link rel="stylesheet" href="https://fonts.googleapis.com/css2?family=Bebas+Neue&family=Heebo:wght@500;600;700&display=swap">
<style>
  :root {
    --navy: #063a5b;
    --maroon: #3f0a24;
    --maroon-deep: #2a0618;
    --gold: #f2a62a;
    --gold-light: #fbc45a;
    --panel: rgba(78, 78, 80, 0.86);
    --line: #d9d9d9;
    --death-red: #ec1c24;
    --white: #ffffff;
    --ink-dark: #1d1d1f;
    --band: rgba(228, 232, 240, 0.93);
    --chevron-gold: #f0a81c;
  }
  html, body {
    margin: 0;
    padding: 0;
    width: 1200px;
    height: 849px;
    overflow: hidden;
    background: #ffffff;
  }
  .poster {
    position: relative;
    width: 1200px;
    height: 849px;
    overflow: hidden;
    font-family: "Heebo", Arial, sans-serif;
  }
  .poster svg { display: block; }
  .title-text {
    font-family: "Bebas Neue", Impact, sans-serif;
    fill: var(--white);
    font-size: 72px;
    letter-spacing: 1px;
  }
  .heaven-text {
    font-weight: 700;
    fill: var(--maroon);
    font-size: 37px;
  }
  .label { fill: var(--white); font-weight: 600; }
  .label-dark { fill: var(--ink-dark); font-weight: 600; }
  .label-gate { fill: #2b2b2b; font-weight: 500; font-size: 16.5px; }
  .label-eden { fill: #3a3a3c; font-weight: 600; font-size: 28px; }
</style>
</head>
<body>
<div class="poster">
<svg width="1200" height="849" viewBox="0 0 1200 849" xmlns="http://www.w3.org/2000/svg">
  <defs>
    <linearGradient id="sceneGrad" x1="0" y1="0" x2="0" y2="1">
      <stop offset="0" stop-color="#8fb3cf"/>
      <stop offset="0.25" stop-color="#d8dde0"/>
      <stop offset="0.33" stop-color="#f0d6a8"/>
      <stop offset="0.4" stop-color="#4f7f93"/>
      <stop offset="0.58" stop-color="#6e8f98"/>
      <stop offset="0.72" stop-color="#b8ab94"/>
      <stop offset="1" stop-color="#9c9384"/>
    </linearGradient>
    <linearGradient id="heavenGrad" x1="0" y1="0" x2="1" y2="0">
      <stop offset="0" stop-color="#f7a41f"/>
      <stop offset="0.5" stop-color="#f5ad2f"/>
      <stop offset="1" stop-color="#d99a2e"/>
    </linearGradient>
    <linearGradient id="tormentGrad" x1="0" y1="0" x2="0" y2="1">
      <stop offset="0" stop-color="#b3180f"/>
      <stop offset="0.6" stop-color="#e4501a"/>
      <stop offset="1" stop-color="#8a1a0c"/>
    </linearGradient>
    <linearGradient id="paradiseGrad" x1="0" y1="0" x2="0" y2="1">
      <stop offset="0" stop-color="#c99a4a"/>
      <stop offset="0.45" stop-color="#f6dd9a"/>
      <stop offset="1" stop-color="#a9762c"/>
    </linearGradient>
    <radialGradient id="earthGrad" cx="0.4" cy="0.35" r="0.7">
      <stop offset="0" stop-color="#5f9a5a"/>
      <stop offset="0.5" stop-color="#2a5f9e"/>
      <stop offset="1" stop-color="#173d78"/>
    </radialGradient>
    <radialGradient id="oldEarthGrad" cx="0.5" cy="0.4" r="0.7">
      <stop offset="0" stop-color="#3f7d86"/>
      <stop offset="0.6" stop-color="#23434c"/>
      <stop offset="1" stop-color="#3b2f25"/>
    </radialGradient>
    <radialGradient id="spiritGrad" cx="0.5" cy="0.5" r="0.6">
      <stop offset="0" stop-color="#ffffff"/>
      <stop offset="0.45" stop-color="#b06a92"/>
      <stop offset="1" stop-color="#4a0b2e"/>
    </radialGradient>
    <clipPath id="clipLeftRealm"><circle cx="345" cy="447" r="112"/></clipPath>
    <clipPath id="clipOldEarth"><circle cx="345" cy="728" r="85"/></clipPath>
    <clipPath id="clipNowEarth"><circle cx="939" cy="447" r="112"/></clipPath>
    <clipPath id="clipRightRealm"><circle cx="942" cy="724" r="86"/></clipPath>
  </defs>

  <!-- backdrop scene -->
  <rect class="backdrop" x="0" y="0" width="1200" height="849" fill="url(#sceneGrad)" role="img" aria-label="Photograph of a sunset sky with gulls over the ocean and a sandy beach"/>

  <!-- falling figure area -->
  <rect x="6" y="6" width="100" height="266" rx="6" fill="#3a2a2e" opacity="0.35" role="img" aria-label="Illustration of a human silhouette falling from light"/>

  <!-- title -->
  <rect x="108" y="25" width="743" height="81" rx="8" fill="var(--navy)"/>
  <text class="title-text" x="479" y="92" text-anchor="middle">CURRENT STATE OF MAN'S SOUL</text>

  <!-- heaven band -->
  <rect x="113" y="137" width="1056" height="89" rx="11" fill="url(#heavenGrad)" stroke="var(--maroon)" stroke-width="1.5"/>
  <text class="heaven-text" x="644" y="198" text-anchor="middle">3rd Heaven - God’s Heavenly Throne</text>

  <!-- timeline panels -->
  <rect x="87" y="272" width="476" height="337" rx="10" fill="var(--panel)"/>
  <rect x="750" y="272" width="414" height="337" rx="10" fill="var(--panel)"/>

  <!-- divider between Hades and the Saviour's death -->
  <path d="M461 272 V395 Q461 410 446 410" fill="none" stroke="var(--line)" stroke-width="1.5"/>
  <line x1="420" y1="461" x2="554" y2="461" stroke="var(--line)" stroke-width="1.5"/>

  <!-- death line -->
  <rect x="87" y="589" width="1077" height="20" rx="4" fill="var(--death-red)"/>
  <rect x="119" y="563" width="97" height="26" rx="3" fill="var(--death-red)"/>
  <text class="label" x="166" y="586" text-anchor="middle" font-size="22" font-weight="700">DEATH</text>

  <!-- gate lines -->
  <g stroke="var(--line)" stroke-width="1.5">
    <line x1="285" y1="540" x2="285" y2="652"/>
    <line x1="341" y1="540" x2="341" y2="652"/>
    <line x1="377" y1="540" x2="377" y2="652"/>
    <line x1="407" y1="540" x2="407" y2="652"/>
    <line x1="874" y1="540" x2="874" y2="648"/>
    <line x1="930" y1="540" x2="930" y2="648"/>
    <line x1="969" y1="540" x2="969" y2="648"/>
    <line x1="998" y1="540" x2="998" y2="648"/>
  </g>

  <!-- Hades circle before the Messiah -->
  <g clip-path="url(#clipLeftRealm)">
    <rect x="233" y="335" width="112" height="224" fill="url(#tormentGrad)" role="img" aria-label="Illustration of fiery torment with a red stairway"/>
    <rect x="345" y="335" width="112" height="224" fill="url(#paradiseGrad)" role="img" aria-label="Illustration of a golden gate and stairway in paradise"/>
    <line x1="345" y1="335" x2="345" y2="559" stroke="var(--white)" stroke-width="3"/>
  </g>
  <circle cx="345" cy="447" r="112" fill="none" stroke="var(--white)" stroke-width="2"/>
  <text class="label" x="301" y="390" text-anchor="middle" font-size="18.5">Torment</text>
  <text class="label-dark" x="392" y="390" text-anchor="middle" font-size="18.5">Paradise</text>

  <!-- pre-messiah earth -->
  <g clip-path="url(#clipOldEarth)">
    <rect x="260" y="643" width="170" height="170" fill="url(#oldEarthGrad)" role="img" aria-label="Illustration of a dark, cracked fallen earth"/>
    <rect x="260" y="757" width="170" height="60" fill="var(--band)"/>
  </g>
  <circle cx="345" cy="728" r="85" fill="none" stroke="var(--white)" stroke-width="2"/>
  <text class="label-dark" x="345" y="777" text-anchor="middle" font-size="16.5">Pre-Messiah</text>
  <text class="label-dark" x="345" y="796" text-anchor="middle" font-size="16.5">Fallen Earth</text>

  <!-- left labels -->
  <text class="label" x="342" y="315" text-anchor="middle" font-size="21">Hades/Sheol</text>
  <text class="label" x="160" y="472" text-anchor="middle" font-size="22">Adam</text>
  <text class="label" x="160" y="497" text-anchor="middle" font-size="22">Rebellion</text>
  <text class="label-eden" transform="translate(49 491) rotate(-90)" text-anchor="middle">Eden</text>
  <path d="M62 473 l7 8 l-7 8 M70 473 l7 8 l-7 8" fill="none" stroke="var(--maroon)" stroke-width="3"/>

  <!-- the Saviour's death -->
  <rect x="512" y="277" width="6" height="65" fill="var(--white)"/>
  <rect x="494" y="291" width="42" height="5" fill="var(--white)"/>
  <rect x="511" y="288" width="8" height="38" rx="3" fill="var(--chevron-gold)"/>
  <text class="label" x="515" y="369" text-anchor="middle" font-size="23">ELIAN</text>
  <text class="label" x="515" y="393" text-anchor="middle" font-size="23">DEATH</text>
  <path d="M509 425 l-8 10 l8 10 M520 425 l-8 10 l8 10" fill="none" stroke="var(--chevron-gold)" stroke-width="4"/>

  <!-- resurrection arrow -->
  <circle cx="562" cy="461" r="10" fill="none" stroke="var(--line)" stroke-width="1.5"/>
  <path d="M562 461 H635 Q645 461 645 451 V262" fill="none" stroke="var(--maroon)" stroke-width="8"/>
  <path d="M629 277 L645 240 L661 277 Z" fill="var(--maroon)"/>
  <rect x="576" y="349" width="132" height="54" rx="7" fill="var(--white)" stroke="var(--maroon-deep)" stroke-width="2"/>
  <text x="642" y="373" text-anchor="middle" font-size="18" font-weight="600" fill="var(--navy)">Elian</text>
  <text x="642" y="396" text-anchor="middle" font-size="18" font-weight="600" fill="var(--navy)">Resurrection</text>

  <!-- holy spirit descends -->
  <rect x="746" y="259" width="130" height="86" rx="9" fill="url(#spiritGrad)"/>
  <text x="811" y="287" text-anchor="middle" font-size="18" font-weight="600" fill="var(--ink-dark)">Holy</text>
  <text x="811" y="305" text-anchor="middle" font-size="18" font-weight="600" fill="var(--ink-dark)">Spirit</text>
  <text x="811" y="324" text-anchor="middle" font-size="18" font-weight="600" fill="var(--ink-dark)">Descends</text>
  <path d="M726 240 V451 Q726 461 736 461 H790" fill="none" stroke="var(--maroon)" stroke-width="8"/>
  <path d="M780 449 L806 461 L780 473 Z" fill="var(--maroon)"/>
  <circle cx="794" cy="461" r="10" fill="none" stroke="var(--line)" stroke-width="1.5"/>

  <!-- current fallen earth -->
  <g clip-path="url(#clipNowEarth)">
    <rect x="827" y="335" width="224" height="224" fill="url(#earthGrad)" role="img" aria-label="Photograph of planet earth with clouds"/>
    <rect x="827" y="484" width="224" height="80" fill="var(--band)"/>
  </g>
  <circle cx="939" cy="447" r="112" fill="none" stroke="var(--white)" stroke-width="2"/>
  <text class="label-dark" x="939" y="510" text-anchor="middle" font-size="20">Current</text>
  <text class="label-dark" x="939" y="535" text-anchor="middle" font-size="20">Fallen Earth</text>

  <!-- believers & non-believers paths -->
  <path d="M1058 461 H1132 Q1142 461 1142 451 V262" fill="none" stroke="var(--maroon)" stroke-width="8"/>
  <path d="M1126 277 L1142 240 L1158 277 Z" fill="var(--maroon)"/>
  <path d="M1058 479 H1122 Q1142 479 1142 499 V706 Q1142 726 1122 726 H1065" fill="none" stroke="var(--maroon)" stroke-width="8"/>
  <path d="M1080 710 L1048 726 L1080 742 Z" fill="var(--maroon)"/>
  <text class="label" x="1122" y="302" text-anchor="end" font-size="22">Believers</text>
  <text class="label" x="1122" y="327" text-anchor="end" font-size="22">in Elian</text>
  <text class="label" x="1129" y="538" text-anchor="end" font-size="22">Non</text>
  <text class="label" x="1129" y="562" text-anchor="end" font-size="22">-Believers</text>

  <!-- Hades circle today -->
  <g clip-path="url(#clipRightRealm)">
    <rect x="856" y="638" width="86" height="172" fill="url(#tormentGrad)" role="img" aria-label="Illustration of fiery torment with a red stairway"/>
    <rect x="942" y="638" width="86" height="172" fill="url(#paradiseGrad)" role="img" aria-label="Illustration of a golden gate and stairway in paradise"/>
    <line x1="942" y1="638" x2="942" y2="810" stroke="var(--white)" stroke-width="3"/>
  </g>
  <circle cx="942" cy="724" r="86" fill="none" stroke="var(--white)" stroke-width="2"/>
  <text class="label" x="908" y="680" text-anchor="middle" font-size="14.5">Torment</text>
  <text class="label-dark" x="979" y="680" text-anchor="middle" font-size="14.5">Paradise</text>
  <text x="941" y="831" text-anchor="middle" font-size="16.5" font-weight="500" fill="#2b2b2b">Hades/Sheol</text>

  <!-- gates -->
  <text class="label-gate" x="276" y="635" text-anchor="end">Wide Gate</text>
  <text class="label-gate" x="416" y="636">Narrow Gate</text>
  <text class="label-gate" x="864" y="635" text-anchor="end">Wide Gate</text>
  <text class="label-gate" x="1010" y="635">Narrow Gate</text>
  <g fill="none" stroke="var(--maroon)" stroke-width="3">
    <path d="M304 628 l8 -7 l8 7 M304 636 l8 -7 l8 7"/>
    <path d="M384 629 l8 -7 l8 7 M384 637 l8 -7 l8 7"/>
    <path d="M893 628 l8 -7 l8 7 M893 636 l8 -7 l8 7"/>
    <path d="M974 628 l8 -7 l8 7 M974 636 l8 -7 l8 7"/>
  </g>
</svg>
</div>
</body>
</html>
```